Card design for orthopaedic surgeons working as The Brightwater Joint Centre

Business cards, letterhead

Colors

Designer to choose colors to be used in the design.

Requirements
Must have
• Late addition.
• Cards letterhead must have logos of
• Crestmoor Lindell College of Surgeons
• Varenwood Bone Health Association
Nice to have
• Back of card to have space for appointment time to be added by hand and some blank space for writing incidental other notes.

```html
<!DOCTYPE html>
<html lang="en">
<head>
<meta charset="utf-8">
<title>The Brightwater Joint Centre – Business Card</title>
<link rel="stylesheet" href="https://fonts.googleapis.com/css2?family=Ubuntu:wght@300;400;500&display=swap">
<style>
  :root {
    --page-bg: #d9d6d2;
    --card-frost-top: #f1f2f3;
    --card-frost-bottom: #dfe3e7;
    --navy-dark: #0f1a24;
    --navy-mid: #1c2b3a;
    --accent-blue: #2b7fd6;
    --accent-blue-deep: #1e5fae;
    --silver: #c9cfd6;
    --badge-fill: #56677a;
    --text-dark: #3a4048;
    --text-logo: #8d9bab;
  }
  * { margin: 0; padding: 0; box-sizing: border-box; }
  html, body {
    width: 1200px;
    height: 969px;
    overflow: hidden;
    background: var(--page-bg);
    font-family: "Ubuntu", Arial, sans-serif;
  }
  .business-card {
    position: absolute;
    left: 156px;
    top: 224px;
    width: 926px;
    height: 528px;
    border-radius: 26px;
    overflow: hidden;
    background: linear-gradient(160deg, var(--card-frost-top), var(--card-frost-bottom));
    box-shadow: 0 10px 30px rgba(0, 0, 0, 0.18);
  }
  .card-wave {
    position: absolute;
    inset: 0;
    width: 100%;
    height: 100%;
  }
  .contact-block {
    position: absolute;
    left: 60px;
    top: 52px;
    color: var(--text-dark);
  }
  .person-name {
    font-size: 28px;
    font-weight: 500;
    letter-spacing: 1.2px;
    color: var(--accent-blue);
    line-height: 1.1;
  }
  .person-title {
    font-size: 19px;
    font-weight: 400;
    margin-top: 5px;
  }
  .postal-address {
    font-style: normal;
    font-size: 20px;
    font-weight: 300;
    line-height: 25px;
    margin-top: 16px;
  }
  .contact-list {
    list-style: none;
    margin-top: 16px;
  }
  .contact-list li {
    display: flex;
    align-items: center;
    height: 26px;
    font-size: 20px;
    font-weight: 300;
  }
  .contact-list li.contact-small { font-size: 18px; }
  .contact-icon {
    width: 18px;
    height: 18px;
    margin-right: 13px;
    fill: var(--accent-blue);
  }
  .association-badges {
    position: absolute;
    left: 40px;
    bottom: 30px;
    display: flex;
    gap: 14px;
  }
  .association-badge {
    width: 36px;
    height: 36px;
    border-radius: 50%;
    background: var(--badge-fill);
  }
  .centre-name {
    position: absolute;
    right: 52px;
    bottom: 46px;
    font-size: 31px;
    font-weight: 300;
    color: var(--text-logo);
    letter-spacing: -0.3px;
    white-space: nowrap;
  }
</style>
</head>
<body>
  <article class="business-card">
    <svg class="card-wave" viewBox="0 0 918 523" preserveAspectRatio="none" aria-hidden="true">
      <defs>
        <linearGradient id="waveFill" x1="0" y1="0" x2="1" y2="1">
          <stop offset="0" stop-color="#1c2b3a"/>
          <stop offset="1" stop-color="#0f1a24"/>
        </linearGradient>
      </defs>
      <path d="M0,440 C150,470 300,420 450,320 C600,215 760,178 918,225 L918,523 L0,523 Z" fill="url(#waveFill)"/>
      <path d="M0,432 C160,462 300,410 450,306 C600,202 700,182 790,186" fill="none" stroke="#c9cfd6" stroke-width="3"/>
      <path d="M120,458 C250,455 340,395 455,312 C590,212 700,190 790,188" fill="none" stroke="#2b7fd6" stroke-width="4"/>
      <path d="M0,437 C150,462 300,418 440,330" fill="none" stroke="#1e5fae" stroke-width="2"/>
    </svg>

    <div class="contact-block">
      <h1 class="person-name">DANIEL HARROW</h1>
      <p class="person-title">President</p>
      <address class="postal-address">2140 Fernbrook Road<br>Juneau, Alaska 99801</address>
      <ul class="contact-list">
        <li>
          <svg class="contact-icon" viewBox="0 0 24 24" aria-hidden="true"><path d="M6.6 10.8a15.1 15.1 0 0 0 6.6 6.6l2.2-2.2a1 1 0 0 1 1-.25 11.4 11.4 0 0 0 3.6.57 1 1 0 0 1 1 1V20a1 1 0 0 1-1 1A17 17 0 0 1 3 4a1 1 0 0 1 1-1h3.5a1 1 0 0 1 1 1c0 1.25.2 2.45.57 3.57a1 1 0 0 1-.25 1z"/></svg>
          555-214-7730
        </li>
        <li>
          <svg class="contact-icon" viewBox="0 0 24 24" aria-hidden="true"><path d="M7 1h10a2 2 0 0 1 2 2v18a2 2 0 0 1-2 2H7a2 2 0 0 1-2-2V3a2 2 0 0 1 2-2zm0 3v14h10V4zm5 15.5a1.2 1.2 0 1 0 0 2.4 1.2 1.2 0 0 0 0-2.4z"/></svg>
          555-318-6042
        </li>
        <li>
          <svg class="contact-icon" viewBox="0 0 24 24" aria-hidden="true"><path d="M7 3h10v5H7zM4 9h16a2 2 0 0 1 2 2v6h-4v4H6v-4H2v-6a2 2 0 0 1 2-2zm4 7v3h8v-3z"/></svg>
          555-402-9187
        </li>
        <li class="contact-small">
          <svg class="contact-icon" viewBox="0 0 24 24" aria-hidden="true"><path d="M3 5h18a1 1 0 0 1 1 1v12a1 1 0 0 1-1 1H3a1 1 0 0 1-1-1V6a1 1 0 0 1 1-1zm9 7.5L20 7H4z"/></svg>
          daniel@brightwaterjoint.com
        </li>
        <li class="contact-small">
          <svg class="contact-icon" viewBox="0 0 24 24" aria-hidden="true"><path d="M12 2a10 10 0 1 0 0 20 10 10 0 0 0 0-20zm-1 17.9A8 8 0 0 1 4.1 11H8c.2 3.2 1.3 6.2 3 8.9zM8 9H4.1A8 8 0 0 1 11 4.1C9.3 6.8 8.2 6 8 9zm5 10.9c1.7-2.7 2.8-5.7 3-8.9h3.9a8 8 0 0 1-6.9 8.9zM16 9c-.2-3-1.3-2.2-3-4.9A8 8 0 0 1 19.9 9z"/></svg>
          www.brightwaterjoint.com
        </li>
      </ul>
    </div>

    <div class="association-badges">
      <div class="association-badge" role="img" aria-label="Crestmoor Lindell College of Surgeons membership badge"></div>
      <div class="association-badge" role="img" aria-label="Varenwood Bone Health Association membership badge"></div>
    </div>

    <p class="centre-name">The Brightwater Joint Centre</p>
  </article>
</body>
</html>
```